Business Card Design Project

- makeup artist business card

- original and creative

- Elegant design

- Feel free to come out with cool designs but stick to being elegant and attractive

- Design relates to makeup

- includes name, occupation, contact numbers, email, website

- regular size business card

- round corner card

- double sided

- on 1 side it should just have the website name in the center " moonveilstudio.net "

Industry/Entity Type

Business

Requirements
Must have
• Delia Marsh
Makeup Artist
USA: +1 (415)772-0461
Singapore: +65 82307915
deliamarsh@moonveilstudio.net
www.moonveilstudio.net
Should not have
• nothing cartoon looking.
Pictures of makeup being grab from the internet.. Examples: eyes or lips.

```html
<!DOCTYPE html>
<html lang="en">
<head>
<meta charset="utf-8">
<title>Delia Marsh – Makeup Artist Business Card</title>
<link rel="stylesheet" href="https://fonts.googleapis.com/css2?family=Arimo:ital,wght@0,400;1,400&family=Tinos:wght@700&display=swap">
<style>
  :root {
    --canvas-bg: #e6e4e5;
    --plum: #8a1f5f;
    --plum-light: #a83278;
    --plum-dark: #6b1549;
    --band-edge: #3a1a2c;
    --card-white: #ffffff;
    --ink: #333333;
    --ink-soft: #4a4a4a;
    --on-plum: #ffffff;
  }
  * { margin: 0; padding: 0; box-sizing: border-box; }
  html, body {
    width: 1200px;
    height: 944px;
    overflow: hidden;
    background: var(--canvas-bg);
  }
  .canvas {
    position: relative;
    width: 1200px;
    height: 944px;
  }
  .card {
    position: absolute;
    left: 250px;
    width: 700px;
    height: 400px;
    border-radius: 26px;
    overflow: hidden;
    box-shadow: 0 6px 18px rgba(0,0,0,0.18);
  }

  /* Back side */
  .card--back {
    top: 52px;
    background: radial-gradient(ellipse at 45% 40%, var(--plum-light) 0%, var(--plum) 55%, var(--plum-dark) 100%);
    display: flex;
    align-items: center;
    justify-content: center;
  }
  .web-line {
    display: flex;
    align-items: center;
    gap: 14px;
    color: var(--on-plum);
    font-family: "Arimo", Arial, sans-serif;
    font-size: 30px;
    letter-spacing: 2px;
  }
  .web-line .dots {
    display: flex;
    align-items: center;
    gap: 7px;
  }
  .dots span {
    display: block;
    border-radius: 50%;
    background: var(--on-plum);
  }
  .dots span:nth-child(1) { width: 3px; height: 3px; }
  .dots span:nth-child(2) { width: 4px; height: 4px; }
  .dots span:nth-child(3) { width: 5px; height: 5px; }
  .dots span:nth-child(4) { width: 7px; height: 7px; }

  /* Front side */
  .card--front {
    top: 492px;
    background: var(--card-white);
  }
  .brand-name {
    position: absolute;
    left: 44px;
    top: 40px;
    font-family: "Arimo", Arial, sans-serif;
    font-weight: 400;
    font-size: 40px;
    line-height: 1;
    white-space: nowrap;
    color: var(--plum);
  }

  .person {
    position: absolute;
    right: 62px;
    top: 88px;
    text-align: left;
  }
  .person-name {
    font-family: "Tinos", "Times New Roman", serif;
    font-weight: 700;
    font-size: 25px;
    color: var(--plum);
  }
  .person-role {
    font-family: "Arimo", Arial, sans-serif;
    font-style: italic;
    font-size: 15px;
    color: var(--ink-soft);
    margin-top: 2px;
  }

  .contacts {
    position: absolute;
    left: 318px;
    top: 206px;
    list-style: none;
    font-family: "Arimo", Arial, sans-serif;
    font-size: 17px;
    color: var(--ink);
  }
  .contacts li {
    display: flex;
    align-items: center;
    gap: 8px;
    height: 23px;
  }
  .contacts svg { width: 14px; height: 14px; flex: none; }

  .band {
    position: absolute;
    left: 0;
    bottom: 0;
    width: 700px;
    height: 120px;
  }
  .card--front .web-line {
    position: absolute;
    left: 0;
    right: 0;
    bottom: 22px;
    justify-content: center;
    font-size: 27px;
  }
</style>
</head>
<body>
<main class="canvas">

  <section class="card card--back" aria-label="Card back">
    <p class="web-line">
      <span class="dots"><span></span><span></span><span></span><span></span></span>
      moonveilstudio.net
    </p>
  </section>

  <section class="card card--front" aria-label="Card front">
    <h1 class="brand-name">moonveil studio</h1>

    <div class="person">
      <h2 class="person-name">Delia Marsh</h2>
      <p class="person-role">Makeup Artist</p>
    </div>

    <ul class="contacts">
      <li>
        <svg viewBox="0 0 14 14" aria-hidden="true"><circle cx="7" cy="7" r="6.3" fill="none" stroke="#8a1f5f" stroke-width="1.2"/><path d="M4.6 3.8c.6-.3 1 .1 1.2.6l.4 1c.1.4-.1.6-.4.8-.2.1-.2.3-.1.5.4.8.9 1.3 1.6 1.7.2.1.4.1.5-.1.2-.3.5-.5.9-.3l.9.5c.4.2.6.7.3 1.2-.5.8-1.4.9-2.3.4-1.5-.8-2.7-2-3.4-3.6-.4-.9-.3-2.2.4-2.7z" fill="#8a1f5f"/></svg>
        USA: +1 (415)772-0461
      </li>
      <li>
        <svg viewBox="0 0 14 14" aria-hidden="true"><circle cx="7" cy="7" r="6.3" fill="none" stroke="#8a1f5f" stroke-width="1.2"/><path d="M4.6 3.8c.6-.3 1 .1 1.2.6l.4 1c.1.4-.1.6-.4.8-.2.1-.2.3-.1.5.4.8.9 1.3 1.6 1.7.2.1.4.1.5-.1.2-.3.5-.5.9-.3l.9.5c.4.2.6.7.3 1.2-.5.8-1.4.9-2.3.4-1.5-.8-2.7-2-3.4-3.6-.4-.9-.3-2.2.4-2.7z" fill="#8a1f5f"/></svg>
        Singapore: +65 82307915
      </li>
      <li>
        <svg viewBox="0 0 14 14" aria-hidden="true"><rect x="1" y="3" width="12" height="8.5" rx="1" fill="#8a1f5f"/><path d="M1.5 3.6 7 8l5.5-4.4" fill="none" stroke="#fff" stroke-width="1.1"/></svg>
        deliamarsh@moonveilstudio.net
      </li>
    </ul>

    <svg class="band" viewBox="0 0 700 120" preserveAspectRatio="none" aria-hidden="true">
      <defs>
        <linearGradient id="bandFill" x1="0" y1="0" x2="0" y2="1">
          <stop offset="0" stop-color="#9a2a6c"/>
          <stop offset="1" stop-color="#7d1a56"/>
        </linearGradient>
      </defs>
      <path d="M0 10 C 200 30, 430 42, 700 6 L700 120 L0 120 Z" fill="var(--band-edge)"/>
      <path d="M0 18 C 200 38, 430 50, 700 14 L700 120 L0 120 Z" fill="url(#bandFill)"/>
    </svg>

    <p class="web-line">
      <span class="dots"><span></span><span></span><span></span><span></span></span>
      moonveilstudio.net
    </p>
  </section>

</main>
</body>
</html>
```